Restaurant Menu New Design

Hello Designers,

Blue Fern is a casual family oriented dine-in restaurant, we serve American Italian dishes like Pizza, Pasta, and Sandwiches.

We are excited about adding some new delicious dishes and recipes to our menu. And we are looking for a talented and creative designer to design it.

The menu is a 12 page black leather book, page size is:
6.5" X 11.69" (16.51 cm X 29.69 cm)

Below is the scope of work and requirements:

1) Design a completely all new, creative, and beautiful menu, including cover page, blue fern oven intro. page, interior pages, and kids menu page.

2) Design a take out edition of the menu. It will be exactly the same as the dine-in menu, but with the addition of a back cover page with info such as contacts, social media, location map, etc…

3) Files are required in Adobe Illustrator format. Layers should be organized, all text should be editable, and all the food pictures easy to change.

4) This is a two language menu, so you are required to make space in the design for a second language. The easiest way to do that is have every item listed in English twice, then I will edit the second text with Illustrator.

5) In your initial design submission, the minimum you are required to submit are these 4 pages:
– Cover page
– Typical interior menu page
– Kids menu page
– Take-out menu back cover page

If your initial design is selected, then you are required to submit all remaining pages to complete the project.

In the link below, you will find:
1) Logo
2) New menu text in Excel
3) Food images (will take some time to upload)
4) The old dine-in and take out menu designs

https://www.filevaultra.com/sh/kq7tmwzabe3pxd/BBBrTnpLk41QaWmZpQ8V2X7Jd?dl=0

Thank you for stopping by and reading this brief. I hope you like this project and enjoy designing our new menu. Please let me know if you have any questions.

Cheers!

Project Deadline Extended
Reason: We have decided to extend the deadline due to the low number of submissions which was much lower than the expected submissions we were give by Brief Harbor.

```html
<!DOCTYPE html>
<html lang="en">
<head>
<meta charset="utf-8">
<title>Blue Fern – Menu Cover and Pizza Page</title>
<link rel="stylesheet" href="https://fonts.googleapis.com/css2?family=Montserrat:wght@800&family=Roboto:wght@400;700&display=swap">
<style>
  :root {
    --stage: #ece9e2;
    --cover-top: #b3a95a;
    --cover-mid: #c2b976;
    --cover-bottom: #d3cd98;
    --page-top: #efe8bd;
    --page-bottom: #f6f1d4;
    --strip: #f4f4f2;
    --logo-cream: #f3eecd;
    --brown: #6b4a1c;
    --gold: #c9a628;
    --gold-text: #a9851a;
    --desc: #8a6a20;
    --ink: #222;
    --card: #ffffff;
  }
  * { margin: 0; padding: 0; box-sizing: border-box; }
  html, body { width: 1200px; height: 800px; overflow: hidden; }
  body {
    position: relative;
    background: var(--stage);
    font-family: "Roboto", Arial, sans-serif;
  }
  .page {
    position: absolute;
    top: 66px;
    width: 350px;
    height: 674px;
    box-shadow: 0 6px 18px rgba(0,0,0,.18);
  }
  .page::before, .page::after {
    content: "";
    position: absolute;
    left: 0; right: 0;
    height: 22px;
    background: var(--strip);
    z-index: 2;
  }
  .page::before { top: 0; }
  .page::after { bottom: 0; }
  .pattern {
    position: absolute;
    inset: 22px 0;
    background: radial-gradient(circle at 20% 25%, rgba(255,255,255,.06), transparent 40%),
                radial-gradient(circle at 80% 75%, rgba(255,255,255,.06), transparent 40%);
  }

  /* Cover */
  .cover {
    left: 197px;
    background: linear-gradient(180deg, var(--cover-top) 0%, var(--cover-mid) 45%, var(--cover-bottom) 100%);
  }
  .cover-name {
    position: absolute;
    left: 0; right: 0;
    top: 344px;
    text-align: center;
    font-family: "Montserrat", Arial, sans-serif;
    font-weight: 800;
    font-size: 42px;
    line-height: 1;
    letter-spacing: 1px;
    color: var(--logo-cream);
  }
  .cover-rule {
    position: absolute;
    left: 36px; right: 0;
    top: 347px;
    margin-top: 0;
    transform: translateY(66px);
    height: 1px;
    background: var(--logo-cream);
    opacity: .8;
  }

  /* Pizza page */
  .menu-page {
    left: 645px;
    background: linear-gradient(180deg, var(--page-top), var(--page-bottom));
  }
  .section-title {
    position: absolute;
    left: 117px;
    top: 22px;
    width: 116px;
    height: 36px;
    background: var(--brown);
    color: var(--logo-cream);
    font-family: "Montserrat", Arial, sans-serif;
    font-weight: 800;
    font-size: 23px;
    line-height: 36px;
    text-align: center;
    z-index: 3;
  }
  .menu-card {
    position: absolute;
    left: 41px;
    top: 97px;
    width: 267px;
    height: 480px;
    background: var(--card);
    box-shadow: 0 4px 14px rgba(0,0,0,.25);
    padding: 14px 10px 0 8px;
    z-index: 1;
  }
  .dish {
    position: relative;
    height: 37.7px;
    display: flex;
    justify-content: space-between;
    padding-top: 4px;
    border-bottom: 1.5px solid var(--gold);
  }
  .dish:last-child { border-bottom: none; }
  .dish-en { width: 43%; }
  .dish-alt { width: 43%; text-align: right; }
  .dish-name {
    font-size: 7px;
    font-weight: 700;
    letter-spacing: .2px;
    color: var(--ink);
    text-transform: uppercase;
    line-height: 1.2;
  }
  .dish-alt .dish-name { color: var(--gold-text); }
  .dish-desc {
    font-size: 5.5px;
    line-height: 1.25;
    color: var(--desc);
    margin-top: 1px;
  }
  .dish-alt .dish-desc { color: #333; }
  .price {
    position: absolute;
    left: 259px;
    top: 3px;
    width: 42px;
    height: 26px;
    background: var(--gold);
    color: #fff;
    font-size: 9px;
    font-weight: 700;
    line-height: 26px;
    padding-left: 9px;
  }
  .page-name {
    position: absolute;
    left: 0; right: 0;
    top: 612px;
    text-align: center;
    font-family: "Montserrat", Arial, sans-serif;
    font-weight: 800;
    font-size: 21px;
    line-height: 1;
    color: var(--gold);
  }
</style>
</head>
<body>

<section class="page cover">
  <div class="pattern" role="img" aria-label="Faint pattern of pizza, sandwich, burger and pasta icons"></div>
  <h1 class="cover-name">BLUE FERN</h1>
  <div class="cover-rule"></div>
</section>

<section class="page menu-page">
  <div class="pattern" role="img" aria-label="Faint pizza icon pattern"></div>
  <h2 class="section-title">PIZZA .</h2>
  <div class="menu-card">
    <div class="dish"><div class="dish-en"><p class="dish-name">Spicy Beef</p><p class="dish-desc">Spicy ground beef, pepperoni, white onions, bell peppers, and cilantro</p></div><div class="dish-alt"><p class="dish-name">Spicy Beef</p><p class="dish-desc">Spicy ground beef, pepperoni, white onions, bell peppers, and cilantro</p></div><span class="price">37</span></div>
    <div class="dish"><div class="dish-en"><p class="dish-name">BBQ Chicken</p><p class="dish-desc">BBQ chicken, mozzarella, cilantro, red onions</p></div><div class="dish-alt"><p class="dish-name">BBQ Chicken</p><p class="dish-desc">BBQ chicken, mozzarella, cilantro, red onions</p></div><span class="price">37</span></div>
    <div class="dish"><div class="dish-en"><p class="dish-name">Greek</p><p class="dish-desc">Tomatoes, kalamata olives, green bell peppers, spinach, tomato sauce, mozzarella &amp; crumbled feta cheese</p></div><div class="dish-alt"><p class="dish-name">Greek</p><p class="dish-desc">Tomatoes, kalamata olives, green bell peppers, spinach, tomato sauce, mozzarella &amp; crumbled feta cheese</p></div><span class="price">35</span></div>
    <div class="dish"><div class="dish-en"><p class="dish-name">Mushrooms</p><p class="dish-desc">Mushrooms, tomato sauce, mozzarella</p></div><div class="dish-alt"><p class="dish-name">Mushrooms</p><p class="dish-desc">Mushrooms, tomato sauce, mozzarella</p></div><span class="price">34</span></div>
    <div class="dish"><div class="dish-en"><p class="dish-name">Hawaiian</p><p class="dish-desc">Pineapples, bacon, red onions, tomato sauce, mozzarella cheese</p></div><div class="dish-alt"><p class="dish-name">Hawaiian</p><p class="dish-desc">Pineapples, bacon, red onions, tomato sauce, mozzarella cheese</p></div><span class="price">37</span></div>
    <div class="dish"><div class="dish-en"><p class="dish-name">Shrimp Fajita</p><p class="dish-desc">Fajita shrimps, tomato sauce, mozzarella &amp; cheddar cheese, onions, green &amp; red bell peppers, cilantro</p></div><div class="dish-alt"><p class="dish-name">Shrimp Fajita</p><p class="dish-desc">Fajita shrimps, tomato sauce, mozzarella &amp; cheddar cheese, onions, green &amp; red bell peppers, cilantro</p></div><span class="price">42</span></div>
    <div class="dish"><div class="dish-en"><p class="dish-name">Steak Pizza</p><p class="dish-desc">Thinly sliced beef, sautéed onions &amp; mushrooms, tomato sauce, mozzarella cheese</p></div><div class="dish-alt"><p class="dish-name">Steak Pizza</p><p class="dish-desc">Thinly sliced beef, sautéed onions &amp; mushrooms, tomato sauce, mozzarella cheese</p></div><span class="price">37</span></div>
    <div class="dish"><div class="dish-en"><p class="dish-name">Veggie</p><p class="dish-desc">Mushrooms, green peppers, onions, black olives</p></div><div class="dish-alt"><p class="dish-name">Veggie</p><p class="dish-desc">Mushrooms, green peppers, onions, black olives</p></div><span class="price">32</span></div>
    <div class="dish"><div class="dish-en"><p class="dish-name">Pepperoni</p><p class="dish-desc">Pepperoni slices, mozzarella cheese, tomato sauce</p></div><div class="dish-alt"><p class="dish-name">Pepperoni</p><p class="dish-desc">Pepperoni slices, mozzarella cheese, tomato sauce</p></div><span class="price">34</span></div>
    <div class="dish"><div class="dish-en"><p class="dish-name">Cheese</p><p class="dish-desc">Mozzarella cheese &amp; tomato sauce</p></div><div class="dish-alt"><p class="dish-name">Cheese</p><p class="dish-desc">Mozzarella cheese &amp; tomato sauce</p></div><span class="price">27</span></div>
    <div class="dish"><div class="dish-en"><p class="dish-name">Beef Teriyaki Pizza</p><p class="dish-desc">Thin slices of Teriyaki beef, sesame, red bell peppers, spring onions, mozzarella cheese</p></div><div class="dish-alt"><p class="dish-name">Beef Teriyaki Pizza</p><p class="dish-desc">Thin slices of Teriyaki beef, sesame, red bell peppers, spring onions, mozzarella cheese</p></div><span class="price">39</span></div>
    <div class="dish"><div class="dish-en"><p class="dish-name">Hawaiian BBQ Chicken</p><p class="dish-desc">BBQ chicken, pineapple, bacon, mozzarella, red onions, cilantro</p></div><div class="dish-alt"><p class="dish-name">Hawaiian BBQ Chicken</p><p class="dish-desc">BBQ chicken, pineapple, bacon, mozzarella, red onions, cilantro</p></div><span class="price">37</span></div>
  </div>
  <p class="page-name">BLUE FERN</p>
</section>

</body>
</html>
```